Creative, Colorful, Dynamic Infographic for Global Non-Profit

We are a global arts and education non-profit in need of an infographic that illustrates four key skills embedded in our work: Curiosity, Listening, Imagination, Postive Action.
We work primarily with educators, students, and artists who use the power of personal stories to build community and connection and to bridge divides.
Our new brand guidelines, logos, and fonts are here: https://stylevault.example/lumen-circle
I've attached a mock-up of the graphic and the required text. (Note the attached design was created by a staff person, your final design does not need to be the same. The color scheme and text of the final design should match the brand guidelines above.)
The graphic will be used for both web and print media and should include the purple Lumen Circle logo (also attached).
Ideally the final design will delight audiences and spark interest in our work.

```html
<!DOCTYPE html>
<html lang="en">
<head>
<meta charset="utf-8">
<title>Lumen Circle – Four Key Skills</title>
<link href="https://fonts.googleapis.com/css2?family=Montserrat:wght@500;600;700;800&display=swap" rel="stylesheet">
<style>
  :root {
    --backdrop: #c3c3c3;
    --paper: #f1f1f1;
    --paper-edge: #e4e4e4;
    --ink: #1e1e1e;
    --purple: #66339a;
    --blue: #236ac4;
    --green: #117a3b;
    --gold: #fbbf45;
    --gold-text: #e0aa2b;
    --box-gold: #f3e7d2;
    --box-blue: #cad7e6;
    --box-green: #c6ded0;
    --box-purple: #dbd1e5;
    --dash: #555;
    --axis: #bdbdbd;
  }
  * { margin: 0; padding: 0; box-sizing: border-box; }
  html, body {
    width: 1200px; height: 1200px; overflow: hidden;
    background: var(--backdrop);
  }
  .canvas {
    width: 1200px; height: 1200px;
    display: flex; align-items: center; justify-content: center;
  }
  .infographic { display: block; width: 1200px; height: 848px; }
  .infographic text { font-family: 'Montserrat', sans-serif; }
  .brand-name { font-size: 46px; font-weight: 600; fill: var(--purple); letter-spacing: 1px; }
  .title-top { font-size: 62px; font-weight: 700; fill: var(--purple); }
  .title-bottom { font-size: 62px; font-weight: 800; fill: var(--ink); }
  .skill-head { font-size: 36px; font-weight: 700; letter-spacing: 1px; }
  .skill-head.curiosity { fill: var(--blue); }
  .skill-head.listening { fill: var(--green); }
  .skill-head.imagination { fill: var(--purple); }
  .skill-head.action { fill: var(--gold-text); }
  .body-copy { font-size: 22px; font-weight: 500; fill: var(--ink); letter-spacing: 0.6px; }
  .flow-note { font-size: 22px; font-weight: 500; fill: var(--ink); letter-spacing: 0.8px; }
  .hub-name { font-size: 30px; font-weight: 700; fill: #fff; }
  .site-url { font-size: 50px; font-weight: 700; fill: #fff; letter-spacing: 7px; }
  .dashed { fill: none; stroke: var(--dash); stroke-width: 2; stroke-dasharray: 7 5; }
  .connector { fill: none; stroke-width: 5; }
  .connector-end { fill: #fff; stroke-width: 4; }
  .hub-ring { filter: drop-shadow(0 4px 8px rgba(0,0,0,0.3)); }
</style>
</head>
<body>
<main class="canvas">
  <svg class="infographic" viewBox="106 360 1720 1216" xmlns="http://www.w3.org/2000/svg" aria-label="Four key skills embedded in our work">
    <defs>
      <linearGradient id="paperTone" x1="0" y1="0" x2="1" y2="1">
        <stop offset="0" stop-color="#ececec"/>
        <stop offset="0.5" stop-color="#f4f4f4"/>
        <stop offset="1" stop-color="#e2e2e2"/>
      </linearGradient>
    </defs>

    <!-- Card surface -->
    <rect class="card" x="106" y="360" width="1720" height="1216" fill="url(#paperTone)"/>

    <!-- Header -->
    <g class="header">
      <circle class="brand-dot" cx="277" cy="488" r="67" fill="var(--purple)"/>
      <text class="brand-name" x="372" y="505">LUMEN CIRCLE</text>
      <line x1="800" y1="424" x2="800" y2="540" stroke="var(--ink)" stroke-width="3"/>
      <text class="title-top" x="830" y="472">FOUR KEY SKILLS</text>
      <text class="title-bottom" x="830" y="540">EMBEDDED IN OUR WORK</text>
    </g>

    <!-- Central axis -->
    <line x1="952" y1="668" x2="952" y2="1292" stroke="var(--axis)" stroke-width="2"/>

    <!-- Cycle arrows -->
    <g class="cycle">
      <path class="cycle-arrow blue" fill="var(--blue)"
        d="M952,733 A240,240 0 0 0 726.5,890.9 L705.8,883.4 L750,973 L817.6,924.1 L796.9,916.6 A165,165 0 0 1 952,808 Z"/>
      <path class="cycle-arrow green" fill="var(--green)" transform="rotate(-90 952 973)"
        d="M952,733 A240,240 0 0 0 726.5,890.9 L705.8,883.4 L750,973 L817.6,924.1 L796.9,916.6 A165,165 0 0 1 952,808 Z"/>
      <path class="cycle-arrow purple" fill="var(--purple)" transform="rotate(-180 952 973)"
        d="M952,733 A240,240 0 0 0 726.5,890.9 L705.8,883.4 L750,973 L817.6,924.1 L796.9,916.6 A165,165 0 0 1 952,808 Z"/>
      <path class="cycle-arrow gold" fill="var(--gold)" transform="rotate(90 952 973)"
        d="M952,733 A240,240 0 0 0 726.5,890.9 L705.8,883.4 L750,973 L817.6,924.1 L796.9,916.6 A165,165 0 0 1 952,808 Z"/>
      <circle class="hub-ring" cx="952" cy="973" r="148" fill="#fff"/>
      <circle class="hub-core" cx="952" cy="973" r="97" fill="var(--purple)"/>
      <text class="hub-name" x="952" y="964" text-anchor="middle">Lumen</text>
      <text class="hub-name" x="952" y="1000" text-anchor="middle">Circle</text>
    </g>

    <!-- Connectors from cycle to skills -->
    <g class="connectors">
      <path class="connector" stroke="var(--blue)" d="M600,913 L665,913 Q690,830 742,776"/>
      <circle class="connector-end" stroke="var(--blue)" cx="748" cy="768" r="10"/>
      <path class="connector" stroke="var(--green)" d="M600,1028 L665,1028 Q690,1115 742,1172"/>
      <circle class="connector-end" stroke="var(--green)" cx="748" cy="1180" r="10"/>
      <path class="connector" stroke="var(--gold)" d="M1298,913 L1235,913 Q1212,830 1161,776"/>
      <circle class="connector-end" stroke="var(--gold)" cx="1155" cy="768" r="10"/>
      <path class="connector" stroke="var(--purple)" d="M1298,1028 L1235,1028 Q1212,1115 1161,1172"/>
      <circle class="connector-end" stroke="var(--purple)" cx="1155" cy="1180" r="10"/>
    </g>

    <!-- Flow: action to curiosity -->
    <g class="flow top">
      <path class="dashed" d="M705,598 L528,598 L528,628"/>
      <polygon points="510,628 548,628 529,652" fill="var(--gold)"/>
      <path class="dashed" d="M1463,645 L1463,611 L1220,611"/>
      <polygon points="1193,611 1220,593 1220,630" fill="var(--gold)"/>
      <rect x="724" y="584" width="451" height="76" fill="var(--box-gold)"/>
      <text class="flow-note" x="950" y="615" text-anchor="middle">Your positive actions will make you</text>
      <text class="flow-note" x="950" y="644" text-anchor="middle">curious about what else is possible.</text>
    </g>

    <!-- Curiosity -->
    <g class="skill curiosity-block">
      <text class="skill-head curiosity" x="615" y="697" text-anchor="end">CURIOSITY</text>
      <text class="body-copy" text-anchor="end">
        <tspan x="612" y="747">Focus on how you can learn</tspan>
        <tspan x="612" y="776">from another’s knowledge and</tspan>
        <tspan x="612" y="805">experience Your curiosity</tspan>
        <tspan x="612" y="834">allows you to listen</tspan>
      </text>
    </g>

    <!-- Flow: curiosity to listening -->
    <g class="flow left">
      <path class="dashed" d="M528,856 L528,905"/>
      <polygon points="510,905 548,905 529,930" fill="var(--blue)"/>
      <rect x="221" y="932" width="392" height="76" fill="var(--box-blue)"/>
      <text class="flow-note" x="580" y="965" text-anchor="end">Your curiosity will allow</text>
      <text class="flow-note" x="580" y="994" text-anchor="end">you to listen.</text>
      <path class="dashed" d="M528,1012 L528,1062"/>
      <polygon points="510,1062 548,1062 529,1088" fill="var(--blue)"/>
    </g>

    <!-- Listening -->
    <g class="skill listening-block">
      <text class="skill-head listening" x="615" y="1130" text-anchor="end">LISTENING</text>
      <text class="body-copy" text-anchor="end">
        <tspan x="613" y="1180">Seek to understand before</tspan>
        <tspan x="613" y="1209">speaking Your listening</tspan>
        <tspan x="613" y="1238">allows you to take in</tspan>
        <tspan x="613" y="1267">new information</tspan>
      </text>
    </g>

    <!-- Flow: listening to imagination -->
    <g class="flow bottom">
      <path class="dashed" d="M528,1280 L528,1337 L705,1337"/>
      <polygon points="705,1318 705,1355 731,1337" fill="var(--green)"/>
      <rect x="728" y="1295" width="451" height="76" fill="var(--box-green)"/>
      <text class="flow-note" x="953" y="1327" text-anchor="middle">Your listening will allow you to take</text>
      <text class="flow-note" x="953" y="1355" text-anchor="middle">in new information.</text>
      <path class="dashed" d="M1183,1337 L1460,1337 L1460,1318"/>
      <polygon points="1460,1291 1480,1318 1441,1318" fill="var(--green)"/>
    </g>

    <!-- Imagination -->
    <g class="skill imagination-block">
      <text class="skill-head imagination" x="1290" y="1130">IMAGINATION</text>
      <text class="body-copy">
        <tspan x="1290" y="1180">Consider possibilities beyond</tspan>
        <tspan x="1290" y="1209">what you know</tspan>
        <tspan x="1290" y="1238">Your imagination can spark</tspan>
        <tspan x="1290" y="1267">positive action</tspan>
      </text>
    </g>

    <!-- Flow: imagination to action -->
    <g class="flow right">
      <path class="dashed" d="M1460,1090 L1460,1045"/>
      <polygon points="1460,1017 1479,1043 1441,1043" fill="var(--purple)"/>
      <rect x="1288" y="932" width="413" height="76" fill="var(--box-purple)"/>
      <text class="flow-note" x="1318" y="962">Your imagination identifies</text>
      <text class="flow-note" x="1318" y="991">positive actions.</text>
      <path class="dashed" d="M1460,930 L1460,884"/>
      <polygon points="1460,855 1479,882 1441,882" fill="var(--purple)"/>
    </g>

    <!-- Positive action -->
    <g class="skill action-block">
      <text class="skill-head action" x="1290" y="697">POSITIVE ACTION</text>
      <text class="body-copy">
        <tspan x="1290" y="747">Show your words and actions</tspan>
        <tspan x="1290" y="776">matter Your positive actions lead</tspan>
        <tspan x="1290" y="805">to curiosity about what else is</tspan>
        <tspan x="1290" y="834">possible</tspan>
      </text>
    </g>

    <!-- Footer band -->
    <g class="footer">
      <path d="M106,1570 Q966,1222 1826,1548 L1826,1576 L106,1576 Z" fill="var(--green)"/>
      <path d="M106,1574 Q966,1240 1826,1556 L1826,1576 L106,1576 Z" fill="#fff"/>
      <path d="M106,1576 Q966,1275 1826,1562 L1826,1576 Z" fill="var(--purple)"/>
      <text class="site-url" x="966" y="1505" text-anchor="middle">www.lumencircle.example</text>
    </g>
  </svg>
</main>
</body>
</html>
```